BOLD & MINIMALIST DESIGN NEEDED

We want a very bold but minimalistic business card design that is impactful and utilizes both sides of the business card. Our current logo is included for your use.

We want bold fonts and good use of negative space. We don't want the logo to overpower the design.

Target Market(s)

Professionals who are building new commercial buildings.

Industry/Entity Type

Construction

Contact Information for Business Card

Name, Title, email, office phone, cell phone, website

Font styles to use
Serif
Sans Serif

Requirements
Must have
• Bold design!

```html
<!DOCTYPE html>
<html lang="en">
<head>
<meta charset="UTF-8">
<title>Summitline Business Card</title>
<link href="https://fonts.googleapis.com/css2?family=Lato:wght@400;700;900&display=swap" rel="stylesheet">
<style>
  :root {
    --stage: #2b2b2b;
    --green: #6aa51f;
    --green-light: #86c232;
    --green-deep: #2f5410;
    --green-mid: #4f7f18;
    --ink: #111111;
    --paper: #ffffff;
    --muted: #333333;
  }
  * { margin: 0; padding: 0; box-sizing: border-box; }
  html, body { width: 1200px; height: 800px; overflow: hidden; }
  body {
    background: var(--stage);
    font-family: "Lato", Arial, sans-serif;
    position: relative;
  }
  .card {
    position: absolute;
    width: 560px;
    height: 320px;
    border-radius: 18px;
    overflow: hidden;
  }
  /* Front side */
  .card-front {
    left: 70px;
    top: 70px;
    background: radial-gradient(ellipse at 40% 25%, var(--green-mid) 0%, var(--green-deep) 85%);
  }
  .front-brand {
    position: absolute;
    left: 40px;
    top: 150px;
    display: flex;
    align-items: center;
    gap: 10px;
    z-index: 2;
  }
  .brand-square {
    width: 22px;
    height: 22px;
    background: var(--green-light);
    flex: none;
  }
  .brand-name {
    font-weight: 900;
    font-size: 30px;
    letter-spacing: 1px;
    text-transform: uppercase;
    white-space: nowrap;
  }
  .front-brand .brand-name { color: var(--paper); }
  .front-mark {
    position: absolute;
    right: 0;
    top: 0;
    width: 250px;
    height: 100%;
    background: linear-gradient(135deg, #0d0d0d 0%, #1a1a1a 45%, var(--green-light) 100%);
    opacity: 0.9;
    z-index: 1;
  }
  /* Back side */
  .card-back {
    left: 570px;
    top: 410px;
    background: var(--paper);
  }
  .back-band {
    position: absolute;
    left: 0;
    right: 0;
    bottom: 0;
    height: 130px;
    background: linear-gradient(180deg, var(--green-light) 0%, var(--green) 100%);
  }
  .back-tab {
    position: absolute;
    right: 0;
    top: 30px;
    width: 22px;
    height: 40px;
    background: var(--green);
  }
  .person {
    position: absolute;
    right: 40px;
    top: 28px;
    text-align: right;
  }
  .person-name {
    color: var(--green);
    font-weight: 900;
    font-size: 28px;
  }
  .person-title {
    color: var(--muted);
    font-size: 14px;
    margin-top: 2px;
  }
  .back-brand {
    position: absolute;
    left: 36px;
    top: 120px;
    display: flex;
    align-items: center;
    gap: 10px;
  }
  .back-brand .brand-name { color: var(--ink); font-size: 32px; }
  .back-brand .brand-square { background: var(--green); }
  .contact-list {
    position: absolute;
    list-style: none;
    color: var(--paper);
    font-size: 15px;
    line-height: 1.55;
  }
  .contact-left { left: 32px; bottom: 22px; }
  .contact-right { right: 32px; bottom: 22px; text-align: right; }
  .contact-list li { display: flex; align-items: center; gap: 8px; }
  .contact-right li { justify-content: flex-end; }
  .contact-list svg { width: 14px; height: 14px; fill: var(--paper); flex: none; }
</style>
</head>
<body>
  <section class="card card-front">
    <div class="front-brand">
      <span class="brand-square"></span>
      <span class="brand-name">Summitline</span>
    </div>
    <div class="front-mark" role="img" aria-label="Large brand mark decoration"></div>
  </section>

  <section class="card card-back">
    <div class="back-band"></div>
    <div class="back-tab"></div>
    <div class="person">
      <div class="person-name">Marcus Ellery</div>
      <div class="person-title">Founder &amp; CEO</div>
    </div>
    <div class="back-brand">
      <span class="brand-square"></span>
      <span class="brand-name">Summitline</span>
    </div>
    <ul class="contact-list contact-left">
      <li><svg viewBox="0 0 24 24"><path d="M6.6 10.8a15 15 0 0 0 6.6 6.6l2.2-2.2a1 1 0 0 1 1-.25 11.4 11.4 0 0 0 3.6.57 1 1 0 0 1 1 1V20a1 1 0 0 1-1 1A17 17 0 0 1 3 4a1 1 0 0 1 1-1h3.5a1 1 0 0 1 1 1c0 1.25.2 2.45.57 3.57a1 1 0 0 1-.25 1z"/></svg>021-555-730-412</li>
      <li><svg viewBox="0 0 24 24"><rect x="6" y="2" width="12" height="20" rx="2"/></svg>044-555-219-864</li>
      <li><svg viewBox="0 0 24 24"><path d="M2 12 22 3l-6 19-4-8z"/></svg>hello@summitline.com</li>
    </ul>
    <ul class="contact-list contact-right">
      <li>4710 Harbor Ridge Blvd 220-B,</li>
      <li>FL 32401</li>
      <li><svg viewBox="0 0 24 24"><circle cx="12" cy="12" r="10"/></svg>www.summitline.com</li>
    </ul>
  </section>
</body>
</html>
```